you will use Ai to Copy the website Brivanta.com to come up with the basic frame work and it will give you the understanding of how I would like Kelbrava.com to be like. Kelbrava.com is a peer to peer rv rental site very similar to both of the other rv rental sites the difference is that are commission based 20% and above per rental and we will be one flat monthly rate and they keep all the earnings. Below is photo that will help you with the color scheme and the look and feel of the design

1 page

```html
<!DOCTYPE html>
<html lang="en">
<head>
<meta charset="utf-8">
<title>Kelbrava.com — Peer to Peer RV Rentals</title>
<link href="https://fonts.googleapis.com/css2?family=Barlow+Condensed:wght@600;700&family=Inter:wght@400;500;600;700&display=swap" rel="stylesheet">
<style>
:root{
  --navy:#0f1d45;
  --navy-ink:#16244f;
  --green:#3f7a1a;
  --green-dark:#336614;
  --green-soft:#eaf1df;
  --mint:#f1f5ea;
  --mist:#f3f5f8;
  --line:#e3e7ee;
  --text:#2c3345;
  --muted:#6b7385;
  --white:#ffffff;
}
*{box-sizing:border-box;margin:0;padding:0}
html,body{width:1200px;height:2856px;overflow:hidden}
body{font-family:"Inter",sans-serif;color:var(--text);background:var(--white);position:relative}
.heading{font-family:"Barlow Condensed",sans-serif;font-weight:700;color:var(--navy-ink);letter-spacing:.2px}
.btn{display:inline-flex;align-items:center;justify-content:center;background:var(--green);color:#fff;font-weight:600;border-radius:4px;text-decoration:none}

/* header */
.site-header{position:absolute;top:0;left:0;width:1200px;height:93px;background:var(--navy);display:flex;align-items:center;padding:0 22px 0 30px}
.brand{display:flex;align-items:center;gap:10px;font-family:"Inter",sans-serif;font-weight:700;font-size:30px;color:#fff}
.brand-dot{width:14px;height:14px;border-radius:50%;background:var(--green)}
.main-nav{margin-left:auto;display:flex;align-items:center;gap:36px;font-size:15px;font-weight:600;color:#fff}
.main-nav .btn{width:84px;height:38px;font-size:15px;margin-left:-12px}

/* hero */
.hero{position:absolute;top:93px;left:0;width:1200px;height:710px}
.hero-photo{position:absolute;inset:0;background:linear-gradient(180deg,#4a5a6a 0%,#3d4c3f 35%,#2e3b2f 60%,#2b3138 100%)}
.hero-photo::after{content:"";position:absolute;right:0;top:140px;width:560px;height:380px;background:radial-gradient(ellipse at 55% 50%,rgba(170,160,140,.35),rgba(0,0,0,0) 70%)}
.hero-copy{position:absolute;left:83px;top:150px;color:#fff}
.hero-copy h1{font-family:"Barlow Condensed",sans-serif;font-weight:700;font-size:50px;line-height:54px}
.hero-copy p{font-size:19px;line-height:30px;margin-top:18px;width:460px}
.search-bar{position:absolute;left:80px;top:425px;width:1040px;height:85px;background:#fff;border-radius:8px;display:flex;align-items:center;padding:0 22px}
.search-field{height:46px;border-right:1px solid var(--line);padding-left:0;display:flex;flex-direction:column;justify-content:space-between}
.search-field:nth-child(1){width:290px}
.search-field:nth-child(2),.search-field:nth-child(3){width:197px;padding-left:18px}
.search-field:nth-child(4){width:212px;padding-left:18px;border-right:none}
.search-field small{font-size:13px;color:var(--muted)}
.search-field span{font-size:15px;color:#7a8190;display:flex;align-items:center;gap:4px}
.search-bar .btn{margin-left:auto;width:115px;height:40px;font-size:15px}
.hero-features{position:absolute;left:194px;top:582px;display:flex;gap:38px;color:#fff}
.feature{display:flex;gap:14px;width:270px}
.feature:nth-child(3){width:250px}
.feature-icon{flex:none;width:54px;height:54px;border-radius:50%;background:rgba(255,255,255,.92);display:flex;align-items:center;justify-content:center}
.feature h3{font-family:"Barlow Condensed",sans-serif;font-size:18px;font-weight:600}
.feature p{font-size:14px;line-height:21px;margin-top:4px;color:#e6e9ef}

/* rv types */
.rv-types{position:absolute;top:803px;left:0;width:1200px;height:307px;text-align:center}
.section-title{font-size:35px;line-height:40px}
.section-sub{font-size:18px;color:var(--text);margin-top:12px}
.rv-types .section-title{margin-top:40px}
.type-row{position:absolute;top:140px;left:95px;display:flex;gap:44px}
.type{width:162px}
.type-img{height:75px;border-radius:8px;background:linear-gradient(180deg,#c9cdd3,#8c939d)}
.type h4{font-size:15px;font-weight:600;color:var(--navy-ink);margin-top:18px}
.type p{font-size:13px;color:var(--muted);margin-top:8px}
.arrow-btn{position:absolute;width:40px;height:40px;border-radius:50%;background:#fff;box-shadow:0 2px 8px rgba(0,0,0,.15);display:flex;align-items:center;justify-content:center}

/* destinations */
.destinations{position:absolute;top:1110px;left:0;width:1200px;height:440px;background:var(--mist);text-align:center}
.destinations .section-title{margin-top:40px}
.dest-row{position:absolute;top:138px;left:74px;display:flex;gap:29px;text-align:left}
.dest{width:239px;height:262px;background:#fff;border-radius:8px;overflow:hidden;box-shadow:0 1px 6px rgba(0,0,0,.06)}
.dest-img{height:190px}
.dest h4{font-size:15px;font-weight:600;color:var(--navy-ink);margin:20px 0 0 14px}
.dest p{font-size:13px;color:var(--muted);margin:10px 0 0 14px}

/* list your rv */
.owners{position:absolute;top:1550px;left:0;width:1200px;height:405px;background:var(--mint)}
.owners-copy{position:absolute;left:83px;top:38px}
.owners-copy h2{font-size:35px;line-height:40px}
.owners-copy .lead{font-size:15px;line-height:24px;margin-top:20px;width:370px}
.checklist{list-style:none;margin-top:18px}
.checklist li{display:flex;align-items:center;gap:12px;font-size:14px;height:33px}
.owners-actions{display:flex;align-items:center;gap:24px;margin-top:22px}
.owners-actions .btn{width:110px;height:36px;font-size:14px}
.owners-actions a.link{font-size:14px;color:var(--green);font-weight:600;text-decoration:underline;display:flex;align-items:center;gap:8px}
.owners-photo{position:absolute;left:540px;top:6px;width:660px;height:375px;border-radius:14px 0 0 14px;background:linear-gradient(135deg,#5d6b3a 0%,#8a8a5c 40%,#b8aa84 60%,#55613a 100%)}

/* how it works */
.how{position:absolute;top:1955px;left:0;width:1200px;height:275px;text-align:center}
.how .section-title{margin-top:30px}
.steps{position:absolute;top:88px;left:123px;display:flex;gap:120px}
.step{width:140px;position:relative}
.step-icon{width:80px;height:80px;border-radius:50%;background:var(--green-soft);margin:0 auto;display:flex;align-items:center;justify-content:center}
.step h4{font-size:16px;font-weight:600;color:var(--navy-ink);margin-top:20px}
.step p{font-size:13px;line-height:20px;color:var(--muted);margin-top:8px}
.step-dash{position:absolute;top:39px;left:172px;width:84px;border-top:2px dashed #c4cad4}

/* testimonials */
.reviews{position:absolute;top:2230px;left:0;width:1200px;height:330px;text-align:center}
.reviews .section-title{margin-top:38px}
.review-row{position:absolute;top:107px;left:75px;display:flex;gap:48px;text-align:left}
.review{width:310px;height:191px;background:#fff;border:1px solid var(--line);border-radius:8px;padding:20px 26px}
.stars{display:flex;gap:4px}
.review blockquote{font-size:15px;line-height:25px;margin-top:16px;height:70px}
.reviewer{display:flex;align-items:center;gap:12px;margin-top:14px}
.avatar{width:34px;height:34px;border-radius:50%;background:linear-gradient(135deg,#b9bfc9,#7d8593)}
.reviewer b{display:block;font-size:13px;font-weight:600;color:var(--navy-ink)}
.reviewer span{font-size:13px;color:var(--muted)}

/* newsletter */
.newsletter{position:absolute;top:2560px;left:74px;width:1037px;height:80px;background:var(--mist);border-radius:8px;display:flex;align-items:center;padding:0 24px}
.newsletter h3{font-size:25px;line-height:28px}
.newsletter p{font-size:14px;margin-top:4px}
.newsletter input{margin-left:auto;width:400px;height:42px;border:1px solid #e6e9ee;border-radius:4px;padding:0 18px;font-family:inherit;font-size:14px;color:#7a8190;background:#fff}
.newsletter .btn{width:106px;height:40px;margin-left:12px;font-size:15px}

/* footer */
.site-footer{position:absolute;top:2651px;left:0;width:1200px;height:205px;background:var(--navy);color:#fff}
.footer-brand{position:absolute;left:88px;top:28px}
.footer-brand .brand{font-size:27px}
.footer-brand p{font-size:12px;line-height:18px;color:#d9deea;width:200px;margin-top:18px}
.socials{display:flex;gap:10px;margin-top:12px}
.socials span{width:24px;height:24px;border-radius:50%;background:#8d97b2}
.footer-col{position:absolute;top:28px}
.footer-col h5{font-size:14px;font-weight:600}
.footer-col ul{list-style:none;margin-top:14px}
.footer-col li{font-size:12px;color:#d9deea;height:22.5px}
.store-badge{width:126px;height:40px;border:1px solid #aab2c8;border-radius:6px;margin-top:14px;background:#0a1434}
.copyright{position:absolute;bottom:10px;width:100%;text-align:center;font-size:13px;color:#d9deea}
</style>
</head>
<body>

<header class="site-header">
  <div class="brand"><span class="brand-dot"></span>Kelbrava.com</div>
  <nav class="main-nav">
    <span>How It Works</span><span>Rent an RV</span><span>List Your RV</span><span>Browse Locations</span>
    <span>Resources ▾</span><span>Log In</span><a class="btn" href="#">Sign Up</a>
  </nav>
</header>

<section class="hero">
  <div class="hero-photo" role="img" aria-label="Class A motorhome parked on a mountain road beside a lake and pine forest"></div>
  <div class="hero-copy">
    <h1>Find the Perfect RV<br>for Your Next Adventure</h1>
    <p>Rent the perfect RV from local owners and explore the open road like never before.</p>
  </div>
  <form class="search-bar">
    <div class="search-field"><small>Location</small><span><svg width="11" height="13" viewBox="0 0 11 13"><path d="M5.5 0a5 5 0 0 0-5 5c0 3.5 5 8 5 8s5-4.5 5-8a5 5 0 0 0-5-5zm0 7a2 2 0 1 1 0-4 2 2 0 0 1 0 4z" fill="#6b7385"/></svg>Where would you like to go?</span></div>
    <div class="search-field"><small>Pick up</small><span>Add dates</span></div>
    <div class="search-field"><small>Drop off</small><span>Add dates</span></div>
    <div class="search-field"><small>Guests</small><span>Add guests</span></div>
    <a class="btn" href="#">Search</a>
  </form>
  <div class="hero-features">
    <div class="feature">
      <div class="feature-icon"><svg width="24" height="24" viewBox="0 0 24 24" fill="none" stroke="#3f7a1a" stroke-width="1.8"><rect x="3" y="7" width="18" height="10" rx="3"/><circle cx="8" cy="18" r="2"/><circle cx="16" cy="18" r="2"/></svg></div>
      <div><h3>Wide Selection</h3><p>Choose from thousands of RVs across the country.</p></div>
    </div>
    <div class="feature">
      <div class="feature-icon"><svg width="24" height="24" viewBox="0 0 24 24" fill="none" stroke="#3f7a1a" stroke-width="1.8"><path d="M12 3l7 3v5c0 5-3.5 8-7 10-3.5-2-7-5-7-10V6z"/><path d="M9 12l2 2 4-4"/></svg></div>
      <div><h3>Safe &amp; Secure</h3><p>Every booking is protected with our insurance.</p></div>
    </div>
    <div class="feature">
      <div class="feature-icon"><svg width="24" height="24" viewBox="0 0 24 24" fill="none" stroke="#3f7a1a" stroke-width="1.8"><circle cx="12" cy="10" r="4"/><path d="M5 20c1.5-3 4-4 7-4s5.5 1 7 4"/><path d="M4 11a8 8 0 0 1 16 0"/></svg></div>
      <div><h3>24/7 Support</h3><p>We're here to help before, during, and after your trip.</p></div>
    </div>
  </div>
</section>

<section class="rv-types">
  <h2 class="heading section-title">Find the Right RV for Your Trip</h2>
  <p class="section-sub">Whatever your adventure, we've got the perfect RV for you.</p>
  <div class="type-row">
    <div class="type"><div class="type-img" role="img" aria-label="Class A motorhome"></div><h4>Class A</h4><p>Sleeps 6 • Full Luxury</p></div>
    <div class="type"><div class="type-img" role="img" aria-label="Class B camper van"></div><h4>Class B</h4><p>Sleeps 2 • Compact</p></div>
    <div class="type"><div class="type-img" role="img" aria-label="Class C motorhome"></div><h4>Class C</h4><p>Sleeps 6 • Versatile</p></div>
    <div class="type"><div class="type-img" role="img" aria-label="Travel trailer"></div><h4>Travel Trailer</h4><p>Sleeps 8 • Towable</p></div>
    <div class="type"><div class="type-img" role="img" aria-label="Fifth wheel trailer"></div><h4>Fifth Wheel</h4><p>Sleeps 6 • Spacious</p></div>
  </div>
  <span class="arrow-btn" style="left:1096px;top:166px"><svg width="10" height="16" viewBox="0 0 10 16"><path d="M2 2l6 6-6 6" fill="none" stroke="#16244f" stroke-width="2"/></svg></span>
</section>

<section class="destinations">
  <h2 class="heading section-title">Popular Destinations</h2>
  <p class="section-sub">Explore popular RV destinations across the country.</p>
  <div class="dest-row">
    <div class="dest"><div class="dest-img" role="img" aria-label="Red rock desert landscape in Moab" style="background:linear-gradient(180deg,#9fc0da,#c5743f 45%,#a4522a)"></div><h4>Moab, Utah</h4><p>120+ RVs</p></div>
    <div class="dest"><div class="dest-img" role="img" aria-label="Mountain lake surrounded by forest in Yellowstone" style="background:linear-gradient(180deg,#a8cbe6,#6f8a9c 40%,#2f6b4c 60%,#2fa3a8)"></div><h4>Yellowstone, WY</h4><p>150+ RVs</p></div>
    <div class="dest"><div class="dest-img" role="img" aria-label="Coastal highway along ocean cliffs at Big Sur" style="background:linear-gradient(120deg,#3f7f8f,#6ea0b0 40%,#7e7a5c 65%,#556b45)"></div><h4>Big Sur, California</h4><p>95+ RVs</p></div>
    <div class="dest"><div class="dest-img" role="img" aria-label="Desert sunset with saguaro cactus near Phoenix" style="background:linear-gradient(180deg,#d86a3a,#f1a24f 45%,#7b4a3a 75%,#3a2a28)"></div><h4>Phoenix, Arizona</h4><p>110+ RVs</p></div>
  </div>
  <span class="arrow-btn" style="left:1100px;top:253px"><svg width="10" height="16" viewBox="0 0 10 16"><path d="M2 2l6 6-6 6" fill="none" stroke="#16244f" stroke-width="2"/></svg></span>
</section>

<section class="owners">
  <div class="owners-copy">
    <h2 class="heading">List Your RV and<br>Start Earning</h2>
    <p class="lead">Join thousands of RV owners earning extra income by sharing their RVs.</p>
    <ul class="checklist">
      <li><svg width="16" height="16" viewBox="0 0 16 16"><circle cx="8" cy="8" r="8" fill="#3f7a1a"/><path d="M4.5 8.2l2.3 2.3 4.7-4.7" fill="none" stroke="#fff" stroke-width="1.8"/></svg>One flat monthly rate</li>
      <li><svg width="16" height="16" viewBox="0 0 16 16"><circle cx="8" cy="8" r="8" fill="#3f7a1a"/><path d="M4.5 8.2l2.3 2.3 4.7-4.7" fill="none" stroke="#fff" stroke-width="1.8"/></svg>Keep all your earnings</li>
      <li><svg width="16" height="16" viewBox="0 0 16 16"><circle cx="8" cy="8" r="8" fill="#3f7a1a"/><path d="M4.5 8.2l2.3 2.3 4.7-4.7" fill="none" stroke="#fff" stroke-width="1.8"/></svg>We take only 20% and above per rental</li>
      <li><svg width="16" height="16" viewBox="0 0 16 16"><circle cx="8" cy="8" r="8" fill="#3f7a1a"/><path d="M4.5 8.2l2.3 2.3 4.7-4.7" fill="none" stroke="#fff" stroke-width="1.8"/></svg>No hidden fees</li>
    </ul>
    <div class="owners-actions">
      <a class="btn" href="#">List Your RV</a>
      <a class="link" href="#">Learn More <svg width="14" height="10" viewBox="0 0 14 10"><path d="M0 5h12M8 1l4 4-4 4" fill="none" stroke="#3f7a1a" stroke-width="1.5"/></svg></a>
    </div>
  </div>
  <div class="owners-photo" role="img" aria-label="Family of four standing in front of their RV at a wooded campsite"></div>
</section>

<section class="how">
  <h2 class="heading section-title">How Kelbrava.com Works</h2>
  <div class="steps">
    <div class="step"><div class="step-icon"><svg width="34" height="34" viewBox="0 0 34 34" fill="none" stroke="#3f7a1a" stroke-width="2.2"><circle cx="14" cy="14" r="9"/><path d="M21 21l8 8"/></svg></div><h4>1. Search</h4><p>Find the perfect RV for your trip.</p><span class="step-dash"></span></div>
    <div class="step"><div class="step-icon"><svg width="34" height="34" viewBox="0 0 34 34" fill="none" stroke="#3f7a1a" stroke-width="2.2"><rect x="5" y="7" width="24" height="22" rx="2"/><path d="M5 13h24M11 4v6M23 4v6M11 19h3M18 19h3M11 24h3"/></svg></div><h4>2. Book</h4><p>Book securely online in minutes.</p><span class="step-dash"></span></div>
    <div class="step"><div class="step-icon"><svg width="38" height="34" viewBox="0 0 38 34" fill="none" stroke="#3f7a1a" stroke-width="2.2"><rect x="3" y="8" width="32" height="17" rx="3"/><path d="M8 13h8v6H8zM21 13h9"/><circle cx="11" cy="27" r="3"/><circle cx="27" cy="27" r="3"/></svg></div><h4>3. Go</h4><p>Pick up your RV and hit the road.</p><span class="step-dash"></span></div>
    <div class="step"><div class="step-icon"><svg width="34" height="34" viewBox="0 0 34 34" fill="none" stroke="#3f7a1a" stroke-width="2.2"><circle cx="17" cy="17" r="13"/><path d="M21 12c-1-1.5-2.5-2-4-2-2.5 0-4 1.3-4 3s1.5 2.6 4 3 4 1.4 4 3.2-1.6 3-4 3c-1.7 0-3.2-.6-4.2-2M17 7v20"/></svg></div><h4>4. Enjoy</h4><p>Make memories and leave a review.</p></div>
  </div>
</section>

<section class="reviews">
  <h2 class="heading section-title">What Our Customers Say</h2>
  <div class="review-row">
    <article class="review">
      <div class="stars"><svg width="86" height="14" viewBox="0 0 86 14" fill="#3f7a1a"><path id="st" d="M7 0l2 4.6 5 .4-3.8 3.3 1.2 4.9L7 10.6 2.6 13.2l1.2-4.9L0 5l5-.4z"/><use href="#st" x="18"/><use href="#st" x="36"/><use href="#st" x="54"/><use href="#st" x="72"/></svg></div>
      <blockquote>"Amazing experience! The RV was perfect for our family trip."</blockquote>
      <div class="reviewer"><span class="avatar" role="img" aria-label="Reviewer portrait"></span><div><b>Dana R.</b><span>Los Angeles, CA</span></div></div>
    </article>
    <article class="review">
      <div class="stars"><svg width="86" height="14" viewBox="0 0 86 14" fill="#3f7a1a"><use href="#st"/><use href="#st" x="18"/><use href="#st" x="36"/><use href="#st" x="54"/><use href="#st" x="72"/></svg></div>
      <blockquote>"Renting was so easy and the owner was super helpful."</blockquote>
      <div class="reviewer"><span class="avatar" role="img" aria-label="Reviewer portrait"></span><div><b>Owen P.</b><span>Denver, CO</span></div></div>
    </article>
    <article class="review">
      <div class="stars"><svg width="86" height="14" viewBox="0 0 86 14" fill="#3f7a1a"><use href="#st"/><use href="#st" x="18"/><use href="#st" x="36"/><use href="#st" x="54"/><use href="#st" x="72"/></svg></div>
      <blockquote>"We had the best vacation thanks to Kelbrava.com!"</blockquote>
      <div class="reviewer"><span class="avatar" role="img" aria-label="Reviewer portrait"></span><div><b>Lena K.</b><span>Austin, TX</span></div></div>
    </article>
  </div>
  <span class="arrow-btn" style="left:1100px;top:186px"><svg width="10" height="16" viewBox="0 0 10 16"><path d="M2 2l6 6-6 6" fill="none" stroke="#16244f" stroke-width="2"/></svg></span>
</section>

<section class="newsletter">
  <div>
    <h3 class="heading">Get Adventure Ideas &amp; Exclusive Offers</h3>
    <p>Sign up for our newsletter and get inspired for your next trip.</p>
  </div>
  <input type="email" value="Enter your email" aria-label="Email address">
  <a class="btn" href="#">Sign Up</a>
</section>

<footer class="site-footer">
  <div class="footer-brand">
    <div class="brand"><span class="brand-dot"></span>Kelbrava.com</div>
    <p>The easiest way to rent or list an RV. Join our community of RV owners and adventurers today.</p>
    <div class="socials"><span></span><span></span><span></span></div>
  </div>
  <div class="footer-col" style="left:379px"><h5>Explore</h5><ul><li>How It Works</li><li>Rent an RV</li><li>List Your RV</li><li>Browse Locations</li><li>Resources</li></ul></div>
  <div class="footer-col" style="left:566px"><h5>Company</h5><ul><li>About Us</li><li>Careers</li><li>Press</li><li>Partner with Us</li><li>Contact Us</li></ul></div>
  <div class="footer-col" style="left:753px"><h5>Support</h5><ul><li>Help Center</li><li>Safety</li><li>Insurance</li><li>Terms of Service</li><li>Privacy Policy</li></ul></div>
  <div class="footer-col" style="left:937px"><h5>Download the App</h5><div class="store-badge"></div><div class="store-badge" style="margin-top:14px"></div></div>
  <p class="copyright">© 2026 kelbrava.com. All rights reserved.</p>
</footer>

</body>
</html>
```